Lorvex Tilo medical cannibis cultivation company

tag - Tilo rise
Lorvex Tilo medical cannabis cultivation - logo is selected- can we please see bold examples with our selection. We are mainly dealing with medical companies and professionals. We would like to be stand out in the crowd with our designs. Welcome any and all attempts. Thanks

Target Market(s)

Medical and Professional

Industry/Entity Type

Medical And Science

Font styles to use
Sans Serif

Colors

Designer to choose colors to be used in the design.

Requirements
Must have
• Bright colour and be bold- Love the teal and magenta that is currently on the dark background design.
Nice to have
• shading and the 3D affect- The shadowed appearance.
Should not have
• Anything related to illegal activity or un professional manners

```html
<!DOCTYPE html>
<html lang="en">
<head>
<meta charset="utf-8">
<title>Lorvex Tilo – Business Card</title>
<link href="https://fonts.googleapis.com/css2?family=Marcellus&family=Tinos&display=swap" rel="stylesheet">
<style>
  :root {
    --bg: #e8e8e8;
    --ink: #0a0a0a;
    --magenta: #9e4e98;
    --teal: #00aee6;
    --steel: #8a9096;
    --white: #ffffff;
  }
  html, body {
    margin: 0;
    padding: 0;
    width: 1125px;
    height: 1200px;
    overflow: hidden;
    background: var(--bg);
  }
  .canvas {
    position: relative;
    width: 1125px;
    height: 1200px;
  }
  .card {
    position: absolute;
    left: 150px;
    width: 800px;
    height: 456px;
    border-radius: 26px;
    overflow: hidden;
    transform: scale(1.031);
    transform-origin: top left;
    background: var(--ink);
  }
  .card--front { top: 98px; background: var(--magenta); }
  .card--back  { top: 631px; }

  .wave { position: absolute; inset: 0; width: 800px; height: 456px; }

  .holder {
    position: absolute;
    left: 45px;
    top: 206px;
    color: var(--white);
  }
  .holder__name {
    font-family: "Marcellus", sans-serif;
    font-size: 29px;
    letter-spacing: 0.5px;
    margin: 0;
    line-height: 1;
    font-weight: 700;
  }
  .holder__role {
    font-family: "Marcellus", sans-serif;
    font-size: 18px;
    font-weight: 700;
    margin: 6px 0 0;
    letter-spacing: 0.3px;
  }
  .address {
    font-family: "Tinos", serif;
    font-size: 18px;
    line-height: 24px;
    margin: 18px 0 0;
    font-style: normal;
  }
  .contacts {
    list-style: none;
    padding: 0;
    margin: 12px 0 0;
    font-family: "Tinos", serif;
    font-size: 18px;
  }
  .contacts li {
    display: flex;
    align-items: center;
    height: 25.5px;
  }
  .contacts svg { width: 17px; height: 17px; margin-right: 12px; fill: var(--white); }

  .brand {
    position: absolute;
    display: flex;
    flex-direction: column;
    align-items: center;
  }
  .brand__ring {
    border: 4px solid var(--steel);
    border-radius: 50%;
    box-sizing: border-box;
  }
  .brand__name {
    font-family: "Marcellus", sans-serif;
    color: var(--teal);
    margin: 0;
    line-height: 1;
    white-space: nowrap;
  }
  .brand__tag {
    display: flex;
    align-items: center;
    font-family: "Marcellus", sans-serif;
    color: var(--steel);
    text-transform: uppercase;
    letter-spacing: 2px;
    white-space: nowrap;
  }
  .brand__tag::before, .brand__tag::after {
    content: "";
    display: block;
    height: 1.5px;
    background: var(--steel);
  }

  .brand--front { left: 505px; top: 52px; width: 230px; }
  .brand--front .brand__ring { width: 132px; height: 132px; }
  .brand--front .brand__name { font-size: 33px; margin-top: 12px; }
  .brand--front .brand__tag { font-size: 15px; margin-top: 2px; }
  .brand--front .brand__tag::before,
  .brand--front .brand__tag::after { width: 42px; margin: 0 6px; }

  .brand--back { left: 200px; top: 108px; width: 400px; }
  .brand--back .brand__ring { width: 168px; height: 168px; }
  .brand--back .brand__name { font-size: 48px; margin-top: 16px; }
  .brand--back .brand__tag { font-size: 21px; margin-top: 2px; }
  .brand--back .brand__tag::before,
  .brand--back .brand__tag::after { width: 58px; margin: 0 8px; }
</style>
</head>
<body>
<main class="canvas">

  <section class="card card--front" aria-label="Card front">
    <svg class="wave" viewBox="0 0 800 456" preserveAspectRatio="none" aria-hidden="true">
      <path d="M15 0 C255 0 318 228 478 340 C612 428 742 388 800 326 L800 0 Z" fill="var(--teal)"/>
      <path d="M15 0 C258 0 330 222 494 330 C624 408 742 372 800 320 L800 0 Z" fill="var(--steel)"/>
      <path d="M40 0 C255 6 320 215 482 318 C604 392 732 352 800 312 L800 0 Z" fill="var(--ink)"/>
    </svg>

    <div class="brand brand--front">
      <div class="brand__ring"></div>
      <p class="brand__name">LORVEX TILO</p>
      <p class="brand__tag">Tilo rise</p>
    </div>

    <div class="holder">
      <h1 class="holder__name">MAREN HOLT</h1>
      <p class="holder__role">CEO/FOUNDER</p>
      <address class="address">2214 Alder Crest Road<br>Fairbanks, Alaska 99712</address>
      <ul class="contacts">
        <li>
          <svg viewBox="0 0 24 24" aria-hidden="true"><path d="M6.6 10.8a15.1 15.1 0 0 0 6.6 6.6l2.2-2.2a1 1 0 0 1 1-.25 11.4 11.4 0 0 0 3.6.57 1 1 0 0 1 1 1V20a1 1 0 0 1-1 1A17 17 0 0 1 3 4a1 1 0 0 1 1-1h3.5a1 1 0 0 1 1 1c0 1.25.2 2.45.57 3.57a1 1 0 0 1-.25 1z"/></svg>
          907 318 4462
        </li>
        <li>
          <svg viewBox="0 0 24 24" aria-hidden="true"><path d="M2 5h20v14H2z M3 6l9 7 9-7" fill="none" stroke="#fff" stroke-width="0"/><path d="M2 5h20v1.5l-10 7-10-7z"/><path d="M2 8.5l10 7 10-7V19H2z"/></svg>
          maren@lorvextilo.com
        </li>
        <li>
          <svg viewBox="0 0 24 24" aria-hidden="true"><circle cx="12" cy="12" r="10"/><path d="M12 2v20M2 12h20M5 6.5c4 2 10 2 14 0M5 17.5c4-2 10-2 14 0" stroke="var(--magenta)" stroke-width="1.6" fill="none"/></svg>
          www.lorvextilo.com
        </li>
      </ul>
    </div>
  </section>

  <section class="card card--back" aria-label="Card back">
    <div class="brand brand--back">
      <div class="brand__ring"></div>
      <p class="brand__name">LORVEX TILO</p>
      <p class="brand__tag">Tilo rise</p>
    </div>
  </section>

</main>
</body>
</html>
```